Executive Taxi firm with Chauffeur service Website

I have my domain name registered and I have started to work on my site but I am struggling. I am just about to get a logo for the company and need a web site that clearly represents the fact we are an executive/luxury brand in private hire vehicles. We offer airport transfers, train station transfers, seaport transfers, holiday transfers and business to business pick up and drop off.

Target Market(s)

Corporate people, holidaymakers looking for a luxury start their holiday. VIPs' and celebrities.

Number of Pages Required

5+ page

Font styles to use
Serif
Sans Serif
Decorative
Script

Colors

Designer to choose colors to be used in the design.

Requirements
Must have
• Home Page, Services, About Us, VIP and Contact us
• Please see www.brivomotors.co.uk I have started it but not happy with it at all.
Nice to have
• Booking form or enquiry form.

```html
<!DOCTYPE html>
<html lang="en">
<head>
<meta charset="utf-8">
<title>Brivo Motors – Executive Travel</title>
<link rel="stylesheet" href="https://fonts.googleapis.com/css2?family=Montserrat:wght@300;400;500;600&family=Open+Sans:ital,wght@0,400;0,600;0,700;1,400&display=swap">
<style>
:root{
  --navy:#0c2a5e;
  --ink:#111;
  --text:#333;
  --white:#fff;
  --red:#c8102e;
  --star:#f2a900;
  --line:#d9d9d9;
  --icon-grey:#8a8a8a;
}
*{box-sizing:border-box;margin:0;padding:0}
html,body{width:1200px;height:2296px;overflow:hidden;background:var(--white)}
body{font-family:"Montserrat",sans-serif;color:var(--text);position:relative}
.abs{position:absolute}

/* header */
.site-header{position:absolute;left:0;top:0;width:1200px;height:80px;background:var(--white)}
.brand{position:absolute;left:112px;top:22px;display:flex;align-items:center;gap:10px;font-family:"Open Sans",sans-serif;font-weight:600;font-size:20px;color:var(--navy)}
.brand-dot{width:26px;height:26px;border-radius:50%;background:var(--navy)}
.main-nav a{position:absolute;top:28px;font-family:"Open Sans",sans-serif;font-size:16px;color:var(--ink);text-decoration:none}
.search{position:absolute;left:1071px;top:29px}

/* hero */
.hero{position:absolute;left:0;top:80px;width:1200px;height:520px;
  background:radial-gradient(ellipse at 60% 40%,#7a5a3a 0%,#4a3322 35%,#2a1d16 70%,#1a1310 100%)}
.hero-sub{position:absolute;top:84px;width:100%;text-align:center;font-weight:300;font-size:27px;color:var(--white)}
.hero-title{position:absolute;top:120px;width:100%;text-align:center;font-family:"Open Sans",sans-serif;font-weight:600;font-size:62px;line-height:84px;color:var(--white)}
.service{position:absolute;top:246px;width:190px;margin-left:-95px;text-align:center;color:var(--white);font-family:"Open Sans",sans-serif;font-weight:600;font-size:16px;line-height:24px}
.service svg{display:block;margin:0 auto 14px;height:48px}
.btn-book{position:absolute;left:526px;top:382px;width:148px;height:45px;background:var(--navy);color:var(--white);font-size:15px;font-weight:500;display:flex;align-items:center;justify-content:center}

/* booking */
.booking{position:absolute;left:0;top:600px;width:1200px;height:370px;
  background:linear-gradient(180deg,#1c3d6e 0%,#163564 50%,#122c55 100%)}
.booking h2{position:absolute;top:50px;width:100%;text-align:center;font-family:"Open Sans",sans-serif;font-weight:600;font-size:36px;color:var(--white)}
.field{position:absolute;width:312px;height:46px;background:var(--white);font-family:"Open Sans",sans-serif;font-size:14px;color:#444;padding:0 16px;display:flex;align-items:center;justify-content:space-between}
.btn-submit{position:absolute;left:444px;top:263px;width:312px;height:48px;border:2px solid var(--white);background:var(--navy);color:var(--white);font-weight:600;font-size:16px;display:flex;align-items:center;justify-content:center}

/* about */
.about h2{position:absolute;left:113px;top:1058px;font-family:"Open Sans",sans-serif;font-weight:700;font-size:43px;color:var(--ink)}
.about p{position:absolute;left:113px;width:636px;font-family:"Open Sans",sans-serif;font-size:13.5px;line-height:31px;color:var(--text)}
.btn-more{position:absolute;left:113px;top:1440px;width:146px;height:43px;background:var(--navy);color:var(--white);font-weight:500;font-size:15px;display:flex;align-items:center;justify-content:center}
.app-visual{position:absolute;left:782px;top:1056px;width:314px;height:441px;border-radius:40px;
  background:radial-gradient(ellipse at 50% 55%,#e6e9ee 0%,#eeeeee 60%,#f7f7f7 100%)}

/* testimonials */
.reviews{position:absolute;left:0;top:1587px;width:1200px;height:453px;
  background:radial-gradient(ellipse at 50% 40%,#3b4150 0%,#262a33 55%,#16181d 100%)}
.arrow{position:absolute;top:198px;width:44px;height:44px}
.card{position:absolute;top:109px;width:403px;height:236px;background:var(--white);border-radius:6px}
.avatar{position:absolute;left:32px;top:22px;width:72px;height:72px;border-radius:50%;background:#d7cfc8}
.rating{position:absolute;right:33px;top:37px;background:var(--red);color:var(--white);font-family:"Open Sans",sans-serif;font-size:15px;width:38px;height:22px;text-align:center;line-height:22px}
.stars{position:absolute;right:33px;top:68px;display:flex;gap:3px}
.quote{position:absolute;left:33px;top:113px;width:340px;font-family:"Open Sans",sans-serif;font-style:italic;font-size:13px;line-height:22px;color:#222;text-align:justify;letter-spacing:-0.1px}
.author{position:absolute;left:33px;top:188px;font-family:"Open Sans",sans-serif;font-weight:600;font-size:16px;color:#333}

/* footer */
.footer-label{position:absolute;font-weight:600;font-size:15px;color:var(--ink)}
.footer-small{position:absolute;font-family:"Open Sans",sans-serif;font-size:13px;color:var(--ink)}
.news-input{position:absolute;left:363px;top:2087px;width:292px;height:42px;border:1px solid #bbb;font-family:"Open Sans",sans-serif;font-size:13px;color:#555;padding-left:14px;display:flex;align-items:center}
.news-send{position:absolute;left:655px;top:2087px;width:72px;height:42px;background:var(--navy);color:var(--white);font-weight:600;font-size:15px;display:flex;align-items:center;justify-content:center}
.footer-rule{position:absolute;left:99px;top:2170px;width:1003px;height:1px;background:var(--line)}
.footer-links{position:absolute;left:113px;top:2204px;font-family:"Open Sans",sans-serif;font-size:13px;color:var(--ink)}
.footer-links span{margin:0 10px;color:#666}
.social{position:absolute;top:2247px;width:18px;height:18px;border-radius:50%;background:var(--icon-grey)}
</style>
</head>
<body>

<header class="site-header">
  <div class="brand"><span class="brand-dot"></span>Brivo Motors</div>
  <nav class="main-nav">
    <a style="left:556px">Home</a>
    <a style="left:649px">Services</a>
    <a style="left:756px">About Us</a>
    <a style="left:872px">VIP</a>
    <a style="left:944px">Contact us</a>
  </nav>
  <svg class="search" width="17" height="17" viewBox="0 0 17 17"><circle cx="7" cy="7" r="5" fill="none" stroke="#111" stroke-width="2.4"/><line x1="10.7" y1="10.7" x2="15.5" y2="15.5" stroke="#111" stroke-width="2.6" stroke-linecap="round"/></svg>
</header>

<section class="hero" role="img" aria-label="Night-time city skyline and lit motorway interchange">
  <div class="hero-sub">Private Hire, Chauffeur and taxi service</div>
  <h1 class="hero-title">Executive Brivo Motors</h1>

  <div class="service" style="left:225px">
    <svg width="64" viewBox="0 0 64 48"><path d="M4 34 L22 30 L40 14 Q50 6 58 8 Q60 14 50 22 L32 34 L20 40 Z" fill="none" stroke="#fff" stroke-width="2.4" stroke-linejoin="round"/><path d="M26 26 L14 20 L10 22 L20 30" fill="none" stroke="#fff" stroke-width="2.2"/><line x1="6" y1="44" x2="40" y2="44" stroke="#fff" stroke-width="2"/></svg>
    Airport Transfers</div>
  <div class="service" style="left:409px">
    <svg width="40" viewBox="0 0 40 52"><rect x="5" y="2" width="30" height="40" rx="6" fill="none" stroke="#fff" stroke-width="2.4"/><rect x="10" y="9" width="20" height="14" rx="2" fill="none" stroke="#fff" stroke-width="2"/><circle cx="13" cy="32" r="2.5" fill="#fff"/><circle cx="27" cy="32" r="2.5" fill="#fff"/><line x1="10" y1="42" x2="5" y2="50" stroke="#fff" stroke-width="2.2"/><line x1="30" y1="42" x2="35" y2="50" stroke="#fff" stroke-width="2.2"/></svg>
    Train Station Transfers</div>
  <div class="service" style="left:594px">
    <svg width="58" viewBox="0 0 58 52"><path d="M4 34 L54 34 L48 46 L10 46 Z" fill="none" stroke="#fff" stroke-width="2.4" stroke-linejoin="round"/><rect x="14" y="22" width="30" height="12" fill="none" stroke="#fff" stroke-width="2.2"/><rect x="21" y="12" width="16" height="10" fill="none" stroke="#fff" stroke-width="2.2"/><line x1="29" y1="2" x2="29" y2="12" stroke="#fff" stroke-width="2.2"/><path d="M2 50 Q8 47 14 50 Q20 53 26 50 Q32 47 38 50 Q44 53 50 50 Q54 48 56 50" fill="none" stroke="#fff" stroke-width="2"/></svg>
    Seaport Transfers</div>
  <div class="service" style="left:778px">
    <svg width="46" viewBox="0 0 46 48"><path d="M8 22 Q14 4 34 8 Q22 10 20 24 Z" fill="none" stroke="#fff" stroke-width="2.2" stroke-linejoin="round"/><line x1="22" y1="14" x2="30" y2="34" stroke="#fff" stroke-width="2.2"/><path d="M4 36 Q10 32 16 36 Q22 40 28 36 Q34 32 42 36" fill="none" stroke="#fff" stroke-width="2.2"/><path d="M4 44 Q10 40 16 44 Q22 48 28 44 Q34 40 42 44" fill="none" stroke="#fff" stroke-width="2.2"/></svg>
    Holiday Transfers</div>
  <div class="service" style="left:961px">
    <svg width="58" viewBox="0 0 58 48"><path d="M4 34 L4 26 Q6 22 12 21 L18 14 Q21 12 26 12 L38 12 Q42 12 45 15 L50 21 Q54 22 54 26 L54 34 Z" fill="none" stroke="#fff" stroke-width="2.4" stroke-linejoin="round"/><circle cx="15" cy="34" r="4.5" fill="none" stroke="#fff" stroke-width="2.2"/><circle cx="43" cy="34" r="4.5" fill="none" stroke="#fff" stroke-width="2.2"/></svg>
    business to business<br>pick up &amp; drop off</div>

  <div class="btn-book">BOOK NOW</div>
</section>

<section class="booking" role="img" aria-label="Dusk view of a chauffeur car in blue tones">
  <h2>Book a Ride with Us</h2>
  <div class="field" style="left:112px;top:122px">First Name</div>
  <div class="field" style="left:444px;top:122px">Last Name</div>
  <div class="field" style="left:776px;top:122px">Email Address</div>
  <div class="field" style="left:112px;top:190px">Phone No</div>
  <div class="field" style="left:444px;top:190px">Date
    <svg width="13" height="13" viewBox="0 0 13 13"><rect x="1" y="2" width="11" height="10" fill="none" stroke="#666" stroke-width="1.4"/><line x1="1" y1="5" x2="12" y2="5" stroke="#666" stroke-width="1.4"/><line x1="4" y1="0" x2="4" y2="3" stroke="#666" stroke-width="1.4"/><line x1="9" y1="0" x2="9" y2="3" stroke="#666" stroke-width="1.4"/></svg></div>
  <div class="field" style="left:776px;top:190px">Time
    <svg width="14" height="14" viewBox="0 0 14 14"><circle cx="7" cy="7" r="5.8" fill="none" stroke="#666" stroke-width="1.4"/><path d="M7 3.5 V7 L9.5 8.5" fill="none" stroke="#666" stroke-width="1.4"/></svg></div>
  <div class="btn-submit">SUBMIT</div>
</section>

<section class="about">
  <h2>Always here for you</h2>
  <p style="top:1134px">We provide airport transfers to and from all major UK airports, seaports, train station transfers and an executive business to business transfer service. Whether you have an individual or group transfer Request, our company-owned fleet offers a choice of options to suit your needs, from luxury saloons and SUV's to 9-seat luxury transporters.</p>
  <p style="top:1278px">We provide a door-to-door convenience from your home, office or hotel straight to any destination of your choice. Pre-booked or last minute we aim to cover any transport requirement. Allports and train station service; All pickups from arrivals will of been briefed as to your exact pickup point, or your chauffeur will be waiting with a name board. We also track your arrival time...</p>
  <div class="btn-more">READ MORE</div>
  <div class="app-visual" role="img" aria-label="Smartphone showing a booking app with a route map"></div>
</section>

<section class="reviews" role="img" aria-label="Blurred car interior with steering wheel">
  <svg class="arrow" style="left:32px" viewBox="0 0 44 44"><circle cx="22" cy="22" r="20" fill="none" stroke="#fff" stroke-width="2.5"/><path d="M25 13 L16 22 L25 31" fill="none" stroke="#fff" stroke-width="3.5"/></svg>
  <svg class="arrow" style="left:1121px" viewBox="0 0 44 44"><circle cx="22" cy="22" r="20" fill="none" stroke="#fff" stroke-width="2.5"/><path d="M19 13 L28 22 L19 31" fill="none" stroke="#fff" stroke-width="3.5"/></svg>

  <div class="card" style="left:176px">
    <div class="avatar" role="img" aria-label="Customer portrait"></div>
    <div class="rating">4.5</div>
    <div class="stars">
      <svg width="16" height="16" viewBox="0 0 20 20"><path d="M10 1 L12.6 7 L19 7.4 L14 11.6 L15.6 18 L10 14.5 L4.4 18 L6 11.6 L1 7.4 L7.4 7 Z" fill="#f2a900"/></svg>
      <svg width="16" height="16" viewBox="0 0 20 20"><path d="M10 1 L12.6 7 L19 7.4 L14 11.6 L15.6 18 L10 14.5 L4.4 18 L6 11.6 L1 7.4 L7.4 7 Z" fill="#f2a900"/></svg>
      <svg width="16" height="16" viewBox="0 0 20 20"><path d="M10 1 L12.6 7 L19 7.4 L14 11.6 L15.6 18 L10 14.5 L4.4 18 L6 11.6 L1 7.4 L7.4 7 Z" fill="#f2a900"/></svg>
      <svg width="16" height="16" viewBox="0 0 20 20"><path d="M10 1 L12.6 7 L19 7.4 L14 11.6 L15.6 18 L10 14.5 L4.4 18 L6 11.6 L1 7.4 L7.4 7 Z" fill="#f2a900"/></svg>
      <svg width="16" height="16" viewBox="0 0 20 20"><path d="M10 1 L12.6 7 L19 7.4 L14 11.6 L15.6 18 L10 14.5 L4.4 18 L6 11.6 L1 7.4 L7.4 7 Z" fill="#f2a900"/></svg>
    </div>
    <p class="quote">At vero eos et accusamus et iusto odio dignissimos ducimus qui blanditiis praesentium voluptatum deleniti atque corrupti quos dolores et quas sed quia non numquam...</p>
    <div class="author">-Lena Hart</div>
  </div>

  <div class="card" style="left:623px">
    <div class="avatar" role="img" aria-label="Customer portrait"></div>
    <div class="rating">4.5</div>
    <div class="stars">
      <svg width="16" height="16" viewBox="0 0 20 20"><path d="M10 1 L12.6 7 L19 7.4 L14 11.6 L15.6 18 L10 14.5 L4.4 18 L6 11.6 L1 7.4 L7.4 7 Z" fill="#f2a900"/></svg>
      <svg width="16" height="16" viewBox="0 0 20 20"><path d="M10 1 L12.6 7 L19 7.4 L14 11.6 L15.6 18 L10 14.5 L4.4 18 L6 11.6 L1 7.4 L7.4 7 Z" fill="#f2a900"/></svg>
      <svg width="16" height="16" viewBox="0 0 20 20"><path d="M10 1 L12.6 7 L19 7.4 L14 11.6 L15.6 18 L10 14.5 L4.4 18 L6 11.6 L1 7.4 L7.4 7 Z" fill="#f2a900"/></svg>
      <svg width="16" height="16" viewBox="0 0 20 20"><path d="M10 1 L12.6 7 L19 7.4 L14 11.6 L15.6 18 L10 14.5 L4.4 18 L6 11.6 L1 7.4 L7.4 7 Z" fill="#f2a900"/></svg>
      <svg width="16" height="16" viewBox="0 0 20 20"><path d="M10 1 L12.6 7 L19 7.4 L14 11.6 L15.6 18 L10 14.5 L4.4 18 L6 11.6 L1 7.4 L7.4 7 Z" fill="#f2a900"/></svg>
    </div>
    <p class="quote">At vero eos et accusamus et iusto odio dignissimos ducimus qui blanditiis praesentium voluptatum deleniti atque corrupti quos dolores et quas sed quia non numquam...</p>
    <div class="author">-Arun Mehta</div>
  </div>
</section>

<footer>
  <div class="footer-label" style="left:113px;top:2087px">STAY CONNECTED</div>
  <div class="footer-small" style="left:113px;top:2112px">Join our newsletter and find out more.</div>
  <div class="news-input">Enter Your Email Address</div>
  <div class="news-send">SEND</div>
  <div class="footer-label" style="left:881px;top:2087px">GET IN TOUCH</div>
  <div class="footer-small" style="left:881px;top:2113px">07700 900461 ,info@brivomotors.co.uk</div>
  <div class="footer-rule"></div>
  <div class="footer-links">Home<span>|</span>Services<span>|</span>About Us<span>|</span>VIP<span>|</span>Contact Us</div>
  <div class="footer-small" style="left:113px;top:2239px">Copyright &nbsp;©&nbsp; 2018 &nbsp;Brivo Motors . &nbsp; All rights reserved.</div>
  <div class="social" style="left:921px"></div>
  <div class="social" style="left:957px"></div>
  <div class="social" style="left:993px"></div>
  <div class="social" style="left:1029px"></div>
  <svg class="abs" style="left:1063px;top:2248px" width="21" height="16" viewBox="0 0 21 16"><rect x="0" y="0" width="21" height="16" rx="1.5" fill="#8a8a8a"/><path d="M1 1.5 L10.5 9 L20 1.5" fill="none" stroke="#fff" stroke-width="1.6"/></svg>
</footer>

</body>
</html>
```